Poster Design Project

About Us
Vexora is a company that specializes in providing communication solutions to the travel market. Our simple vision of “every hotel should have a mobile phone in the guest rooms”, led us to develop a path breaking cost effective mobile phone. With full integration capabilities with the hotels property management system, location based marketing, user locator and other features, this product is unique in addressing the hospitality segment.
Product Placement
The Vexora mobile will be placed in the hotel room on an A4 Sized transparent stand (the transparent stand is attached for your reference. If you notice, the phone will be placed in the jacket on the bottom left and in another jacket on the bottom right will be the brochure. So effectively, the design space available on the A4 brochure is only 60% of the space). The designed poster that we wish designed will be inserted in the A4 sized acrylic stand. The stand would typically be on the bedside table or on the study table of the hotel room. The A4 design should be bright and vibrant in keeping with our logo colors.
Attached is our logo. Also attached is the symbol of our phone that could be used innovatively on the brochure if you think it helps.
Attached is the content for the poster.
Updates
Project Deadline Extended
Reason: Feedback from the management team got delayed, hence the extension. Thanks
Project Deadline Extended
Reason: The delay is in the content finalization.
Industry/Entity Type
Property Management
Look and feel
Each slider illustrates characteristics of the customer's brand and the style your logo design should communicate.

```html
<!DOCTYPE html>
<html lang="en">
<head>
<meta charset="utf-8">
<title>Vexora – Keep Talking Poster</title>
<link rel="stylesheet" href="https://fonts.googleapis.com/css2?family=Roboto:wght@100;300;400&family=Roboto+Condensed:wght@700&display=swap">
<style>
  :root {
    --page: #ffffff;
    --orange: #f7901e;
    --orange-light: #fbab4f;
    --orange-deep: #e98312;
    --ink: #1b1b1b;
    --brand-ink: #3a3a3a;
    --white: #ffffff;
  }
  * { margin: 0; padding: 0; box-sizing: border-box; }
  html, body {
    width: 1170px; height: 1200px; overflow: hidden;
    background: var(--page);
  }
  .canvas { position: relative; width: 1170px; height: 1200px; }
  .poster {
    position: absolute; left: 192px; top: 56px;
    width: 741px; height: 1048px;
    background: var(--orange);
    overflow: hidden;
    font-family: "Roboto", Arial, sans-serif;
  }
  .brand-glow {
    position: absolute; left: 490px; top: 35px; width: 230px; height: 230px;
    border-radius: 50%;
    background: radial-gradient(circle, rgba(255,255,255,0.95) 35%, rgba(255,255,255,0) 70%);
  }
  .brand-dot {
    position: absolute; left: 526px; top: 68px; width: 152px; height: 152px;
    border-radius: 50%; background: var(--orange);
  }
  .brand-name {
    position: absolute; left: 530px; top: 238px; width: 150px; text-align: center;
    font-family: "Roboto Condensed", Arial, sans-serif; font-weight: 700;
    font-size: 38px; color: var(--brand-ink); letter-spacing: -0.5px;
  }
  .headline-tab {
    position: absolute; left: 30px; top: 319px; width: 36px; height: 110px;
    background: rgba(214, 120, 40, 0.55);
  }
  .headline-band {
    position: absolute; left: 78px; top: 319px; width: 663px; height: 110px;
    background: rgba(255, 190, 110, 0.45);
  }
  .headline {
    position: absolute; left: 88px; top: 319px;
    font-weight: 100; font-size: 41px; line-height: 52px; color: var(--white);
    letter-spacing: -0.5px;
  }
  .world-map {
    position: absolute; left: 38px; top: 424px; width: 680px; height: 340px;
  }
  .offer {
    position: absolute; left: 98px; top: 460px;
    list-style: none; font-size: 21px; font-weight: 300; color: var(--ink);
  }
  .offer li { height: 27.7px; line-height: 27.7px; }
  .offer .op { padding-left: 42px; font-weight: 700; font-family: "Roboto Condensed", Arial, sans-serif; }
  .offer strong {
    font-family: "Roboto Condensed", Arial, sans-serif; font-weight: 700; font-size: 24px;
  }
  .tagline {
    position: absolute; left: 105px; top: 808px;
    font-weight: 100; font-size: 26px; color: rgba(255,255,255,0.85); letter-spacing: -0.5px;
  }
  .features {
    position: absolute; left: 94px; top: 925px;
    list-style: none; font-size: 11px; font-weight: 300; color: var(--white); line-height: 13.5px;
  }
  .refer {
    position: absolute; left: 95px; top: 1000px;
    font-family: "Roboto Condensed", Arial, sans-serif; font-weight: 700;
    font-size: 14px; color: var(--white);
  }
</style>
</head>
<body>
<div class="canvas">
  <section class="poster">
    <div class="brand-glow"></div>
    <div class="brand-dot"></div>
    <div class="brand-name">Vexora</div>

    <div class="headline-tab"></div>
    <div class="headline-band"></div>
    <h1 class="headline">Pick up this phone NOW,<br>to keep talking....</h1>

    <svg class="world-map" role="img" aria-label="Dotted world map" viewBox="0 0 680 340">
      <defs>
        <radialGradient id="mapTone" cx="50%" cy="45%" r="60%">
          <stop offset="0" stop-color="#fbb25c" stop-opacity="0.75"/>
          <stop offset="1" stop-color="#f7901e" stop-opacity="0"/>
        </radialGradient>
      </defs>
      <rect width="680" height="340" fill="url(#mapTone)"/>
    </svg>

    <ul class="offer">
      <li><strong>SAVE 80%</strong> on international roaming</li>
      <li class="op">+</li>
      <li>Get a <strong>LOCAL</strong> number</li>
      <li class="op">+</li>
      <li><strong>60 FREE</strong> minutes of international Calls</li>
      <li class="op">+</li>
      <li><strong>60 FREE</strong> minutes of local calls</li>
      <li class="op">=</li>
      <li><strong>499 BHT</strong></li>
    </ul>

    <p class="tagline">Vexora. Keep Talking.</p>

    <ul class="features">
      <li>•Itemized bill on checkout</li>
      <li>•Flexible tariff plans to choose fromExcellent call quality</li>
    </ul>

    <p class="refer">Refer to the brochure for more details</p>
  </section>
</div>
</body>
</html>
```